Harrow Hide Revival Product Label

We need a design for a label to be used on bottles of leather cleaner and conditioner products that will be used in curated kits. We would like it to incorporate our business logo as well as have an area that we can fill in later with the appropriate product name as needed. We would like to see designs that use shades of brown, but we are open to other colors often seen in leather. I am including the Harrow Hide business Logo below, however again we would prefer to have the label in various shades of browns, rather than the red and grey, more like the mock-up that I am also attaching.

*** I am attaching examples of the types of bottles that will be used. They vary in size from 8 oz to 16 oz. if you are designing a label for a spray bottle they are from 16-32 oz. ***

```html
<!DOCTYPE html>
<html lang="en">
<head>
<meta charset="utf-8">
<title>Harrow Hide Revival – Leather Cleaner / Conditioner Label</title>
<link href="https://fonts.googleapis.com/css2?family=Montserrat:wght@600;800&family=Open+Sans:wght@400;600&family=Oswald:wght@500&display=swap" rel="stylesheet">
<style>
  :root {
    --page-bg: #f4f1ec;
    --hide-dark: #2a1408;
    --hide-mid: #5a2c12;
    --hide-warm: #8a4a1c;
    --hide-glow: #b06a2a;
    --gold: #f2c14a;
    --cream: #ffffff;
    --rule: #d9a63a;
  }
  * { margin: 0; padding: 0; box-sizing: border-box; }
  html, body {
    width: 1200px; height: 1200px; overflow: hidden;
    background: var(--page-bg);
  }
  .label {
    position: absolute;
    left: 320px; top: 150px;
    width: 560px; height: 900px;
  }
  .label-shape { position: absolute; inset: 0; width: 560px; height: 900px; }
  .brand {
    position: absolute; right: 36px; top: 70px;
    display: flex; flex-direction: column; align-items: flex-end;
  }
  .brand-dot {
    width: 120px; height: 120px; border-radius: 50%;
    background: var(--cream); margin-right: 40px; margin-bottom: 18px;
  }
  .brand-name {
    font-family: "Montserrat", sans-serif; font-weight: 600;
    font-size: 46px; color: var(--cream); letter-spacing: 1px; line-height: 1;
  }
  .brand-sub {
    font-family: "Montserrat", sans-serif; font-weight: 600;
    font-size: 13px; color: var(--cream); letter-spacing: 3px; margin-top: 6px;
  }
  .product {
    position: absolute; left: 44px; top: 400px;
  }
  .product-name {
    font-family: "Montserrat", sans-serif; font-weight: 800;
    font-size: 104px; color: var(--cream); line-height: 1; letter-spacing: -1px;
  }
  .product-type {
    font-family: "Oswald", sans-serif; font-weight: 500;
    font-size: 44px; color: var(--gold); margin-top: 8px; letter-spacing: 0.5px;
  }
  .benefits {
    position: absolute; left: 44px; top: 610px;
    border-left: 2px solid var(--rule); padding-left: 14px;
    font-family: "Open Sans", sans-serif; font-size: 30px; color: var(--cream);
    line-height: 1.3; height: 190px;
  }
  .volume {
    position: absolute; left: 0; right: 0; bottom: 44px; text-align: center;
    font-family: "Open Sans", sans-serif; font-size: 36px; color: var(--gold);
  }
  .volume strong { font-weight: 600; }
</style>
</head>
<body>
  <div class="label">
    <svg class="label-shape" viewBox="0 0 560 900" role="img" aria-label="Rich brown grained leather texture filling the label">
      <defs>
        <linearGradient id="hide" x1="0" y1="0" x2="1" y2="1">
          <stop offset="0" stop-color="var(--hide-mid)"/>
          <stop offset="0.45" stop-color="var(--hide-glow)"/>
          <stop offset="0.75" stop-color="var(--hide-warm)"/>
          <stop offset="1" stop-color="var(--hide-dark)"/>
        </linearGradient>
        <linearGradient id="shade" x1="0" y1="0" x2="0" y2="1">
          <stop offset="0" stop-color="#1e0d04" stop-opacity="0.15"/>
          <stop offset="1" stop-color="#1e0d04" stop-opacity="0.7"/>
        </linearGradient>
      </defs>
      <path d="M0,230 C140,120 360,40 470,12 Q560,-8 560,90 V870 Q560,900 530,900 H50 Q0,900 0,850 Z" fill="url(#hide)"/>
      <path d="M560,300 C360,360 250,520 330,700 C380,810 300,880 250,900 H530 Q560,900 560,870 Z" fill="url(#shade)"/>
      <path d="M0,480 C120,420 200,380 250,400 C160,460 120,600 160,900 H50 Q0,900 0,850 Z" fill="#1e0d04" opacity="0.35"/>
    </svg>

    <div class="brand">
      <div class="brand-dot"></div>
      <div class="brand-name">HARROW HIDE</div>
      <div class="brand-sub">REVIVAL</div>
    </div>

    <div class="product">
      <h1 class="product-name">LEATHER</h1>
      <p class="product-type">CLEANER / CONDITIONER</p>
    </div>

    <ul class="benefits" style="list-style:none">
      <li>Protects against drying</li>
      <li>Replenishes</li>
      <li>Cleans</li>
    </ul>

    <p class="volume"><strong>24</strong> Fl oz.</p>
  </div>
</body>
</html>
```